Push notification screens at app start up

We have an existing news publication app platform and are adding categories to push notifications.

We need two screens designed (each for Zorbel, Quillet and Android for a total of 6d) that show when the app is first launched.

The workflow of our app:
0. app launch screen while webservices run (no work needed)
1. information screen to the user promoting the benefits of push notification with "Next" button. (see concept attached)
2. Push categories selection screen. This will have list of category types, with on/off switch.

"Select the categories that you wish to receive occasional notices:
Breaking News (on/off switch)
Local News (on/off switch)
Sports (on/off switch)
Local Events (on/off switch)
Weather Alerts (on/off switch)
Local Deals (on/off switch)"

"Enable these categories on the next screen."
"Next" button

Background:
When I was looking around at app designs, I came across this one (http://www.plinthworks.example/design/7719034) and I really liked it. We obviously have different features on our screen, but I’d like to have this same feel. The colors used in this design are perfect.

UPDATE: I do not mean to limit your design to match the layout as the one mentioned above. Please use your creativity for the layout.

Our standard font in Helvetica Neue.

Notes:
- our app is developed for all phone devices from Zorbel 4 to Zorbel 6, so designs should be thoughtful of vertical scrolling if needed.
- our app is developed for Quillets, so we'll need designs completed as well. (We can finalize Zorbel design first, then translate the design to Quillet.)
- our app is developed for Android phones (not tablets), so we'll need designs completed as well. (We can finalize iOS design first, then translater to Android UI design guidelines).

We hope to establish a good on-going relationship with the designer for as-needed work in the future.

News

• Helvetica Neue

• Clean designs. No clutter.
• We would likely go with the standard on/off switches for both iOS and Android, but are open to small custom variations.

```html
<!DOCTYPE html>
<html lang="en">
<head>
<meta charset="utf-8">
<title>Notifications onboarding</title>
<link rel="stylesheet" href="https://fonts.googleapis.com/css2?family=Inter:wght@400;500;700&display=swap">
<style>
  :root {
    --screen-bg: #0a111c;
    --accent: #2166ff;
    --card-bg: #ffffff;
    --title-ink: #333a44;
    --body-ink: #4a5058;
    --status-ink: #ffffff;
  }
  * { box-sizing: border-box; margin: 0; padding: 0; }
  html, body { width: 675px; height: 1200px; overflow: hidden; }
  body {
    background: var(--screen-bg);
    font-family: "Inter", "Helvetica Neue", Arial, sans-serif;
    position: relative;
  }
  .status-bar {
    position: absolute; top: 0; left: 0; width: 675px; height: 44px;
    color: var(--status-ink); font-size: 23px; font-weight: 500;
  }
  .status-bar .carrier {
    position: absolute; left: 12px; top: 10px;
    display: flex; align-items: center; gap: 8px;
  }
  .signal { display: flex; gap: 3px; }
  .signal span {
    width: 11px; height: 11px; border-radius: 50%;
    border: 1.5px solid var(--status-ink);
  }
  .signal span.on { background: var(--status-ink); }
  .status-bar .clock {
    position: absolute; left: 0; right: 0; top: 10px; text-align: center;
  }
  .status-bar .power {
    position: absolute; right: 12px; top: 10px;
    display: flex; align-items: center; gap: 10px;
  }
  .battery {
    width: 46px; height: 21px; border: 2px solid var(--status-ink);
    border-radius: 4px; padding: 2px; position: relative;
  }
  .battery::after {
    content: ""; position: absolute; right: -6px; top: 5px;
    width: 3px; height: 8px; background: var(--status-ink); border-radius: 0 2px 2px 0;
  }
  .battery span { display: block; width: 100%; height: 100%; background: var(--status-ink); border-radius: 1px; }

  .badge {
    position: absolute; left: 258px; top: 92px;
    width: 158px; height: 158px; border-radius: 50%;
    background: var(--accent);
    display: flex; align-items: center; justify-content: center;
  }
  .card {
    position: absolute; left: 27px; top: 412px;
    width: 621px; height: 545px;
    background: var(--card-bg); border-radius: 14px;
    text-align: center;
  }
  .card h1 {
    margin-top: 50px;
    font-size: 42px; font-weight: 700; color: var(--title-ink);
    letter-spacing: -0.3px;
  }
  .card p {
    font-size: 21px; line-height: 29px; color: var(--body-ink);
    padding: 0 40px;
  }
  .card .lead { margin-top: 36px; }
  .card .note { margin-top: 29px; }
  .next-button {
    position: absolute; left: 18px; right: 18px; top: 420px; height: 97px;
    background: var(--accent); color: #fff; border: none; border-radius: 9px;
    font-family: inherit; font-size: 32px; font-weight: 700; letter-spacing: 0.5px;
  }
</style>
</head>
<body>
  <header class="status-bar">
    <div class="carrier">
      <div class="signal"><span class="on"></span><span class="on"></span><span class="on"></span><span></span><span></span></div>
      <span>KESTREL</span>
      <svg width="24" height="18" viewBox="0 0 24 18" aria-hidden="true">
        <path d="M2 6a14 14 0 0 1 20 0M5.5 9.5a9 9 0 0 1 13 0M9 13a4 4 0 0 1 6 0" fill="none" stroke="#fff" stroke-width="2.4" stroke-linecap="round"/>
        <circle cx="12" cy="16" r="1.6" fill="#fff"/>
      </svg>
    </div>
    <div class="clock">4:21 PM</div>
    <div class="power">
      <svg width="12" height="20" viewBox="0 0 12 20" aria-hidden="true">
        <path d="M1 5l10 10-5 4V1l5 4L1 15" fill="none" stroke="#fff" stroke-width="1.6"/>
      </svg>
      <span>100%</span>
      <div class="battery"><span></span></div>
    </div>
  </header>

  <div class="badge">
    <svg width="96" height="80" viewBox="0 0 96 80" aria-hidden="true" fill="none" stroke="#fff" stroke-width="4.5" stroke-linejoin="round" stroke-linecap="round">
      <path d="M14 30h12l30-16v52L26 50H14z"/>
      <path d="M26 30v20"/>
      <path d="M20 50l6 18h10l-4-18"/>
      <path d="M56 14v52"/>
      <path d="M66 30a12 12 0 0 1 0 20"/>
      <path d="M74 22a22 22 0 0 1 0 36"/>
      <path d="M82 15a32 32 0 0 1 0 50"/>
    </svg>
  </div>

  <main class="card">
    <h1>Notifications</h1>
    <p class="lead">By enabling push notifications, you can keep up to date with occasional notifications related to items you care about. Select the categories on the next screen and then authorize the push notifications.</p>
    <p class="note">If you ever change your mind, you can adjust these options in the Settings menu of this app.</p>
    <button class="next-button" type="button">NEXT</button>
  </main>
</body>
</html>
```